Fresh, modern, fun business card for pediatric dental practice

Need a business card for fresh, modern, fun pediatric dental practice

Clean look that matches our website's font and colors

We prefer the look of curved corners on business cards

Target Market(s)

parents (mothers) of young children, professionals, mid-high class

Industry/Entity Type

Dental

Contact Information for Business Card

Maplebrook Pediatric Dentistry
482 Quarry Lane
Suite 517
Elmhaven, PA 17599
717.555.0193
www.maplebrookkidsdental.example

Mei-Ran Tsai, DMD
Corinne Walbeck, DMD
(we are working on our email address, but we would like that on the card as well)

Font styles to use
Sans Serif

Requirements
Must have
• All info; we would also like to make cards for individual staff members
• colors from our website and color palatte, attatched
• use same font and design as website for branding
Nice to have
• clean, simple card that has a pop of color
• we would like to see a few designs with our tag line "where smiles get brighter"
• we are not sure if we want to have it on there or not
• we would like to see a few designs incorporating the ribbon graphic on our website where the word WELCOME is

```html
<!DOCTYPE html>
<html lang="en">
<head>
<meta charset="utf-8">
<title>Maplebrook Pediatric Dentistry – Business Card</title>
<link rel="stylesheet" href="https://fonts.googleapis.com/css2?family=Lato:wght@400;700&family=Roboto:wght@500;700&display=swap">
<style>
  :root {
    --page-bg: #a3a3a3;
    --card-pink: #c9288c;
    --sun-yellow: #f0b323;
    --text-white: #ffffff;
    --card-radius: 15px;
  }
  * { box-sizing: border-box; margin: 0; padding: 0; }
  html, body { width: 1200px; height: 1134px; overflow: hidden; }
  body { background: var(--page-bg); position: relative; font-family: "Lato", sans-serif; }

  .card {
    position: absolute;
    left: 261px;
    width: 675px;
    height: 380px;
    background: var(--card-pink);
    border-radius: var(--card-radius);
  }
  .card--front { top: 161px; }
  .card--back { top: 589px; }

  .brand { position: absolute; text-align: center; color: var(--sun-yellow); font-family: "Lato", sans-serif; font-weight: 700; }
  .brand__dot { display: block; margin: 0 auto 12px; border-radius: 50%; background: var(--sun-yellow); }
  .brand__name { display: block; line-height: 1.05; }
  .card--front .brand { left: 30px; width: 280px; top: 118px; }
  .card--front .brand__dot { width: 34px; height: 34px; }
  .card--front .brand__name--main { font-size: 40px; }
  .card--front .brand__name--sub { font-size: 21px; letter-spacing: 1px; margin-top: 4px; }

  .card--back .brand { left: 0; width: 675px; top: 118px; }
  .card--back .brand__dot { width: 44px; height: 44px; margin-bottom: 16px; }
  .card--back .brand__name--main { font-size: 50px; }
  .card--back .brand__name--sub { font-size: 25px; letter-spacing: 1px; margin-top: 6px; }

  .divider { position: absolute; left: 343px; top: 76px; width: 2px; height: 210px; background: var(--sun-yellow); }

  .dentists { position: absolute; left: 378px; top: 70px; font-family: "Roboto", sans-serif; font-weight: 700; font-size: 26px; line-height: 37px; color: var(--text-white); }
  .dentists .credential { color: var(--sun-yellow); font-weight: 500; }

  .address { position: absolute; left: 378px; top: 155px; font-size: 15.5px; line-height: 22px; color: var(--text-white); }

  .contacts { position: absolute; left: 378px; top: 216px; list-style: none; font-size: 15.5px; color: var(--text-white); }
  .contacts li { display: flex; align-items: center; height: 24.5px; white-space: nowrap; }
  .contacts svg { width: 19px; height: 19px; margin-right: 8px; flex: none; }

  .welcome-ribbon { position: absolute; left: 180px; top: 313px; width: 330px; height: 44px; }
  .welcome-ribbon svg { position: absolute; inset: 0; }
  .welcome-ribbon span { position: absolute; inset: 0; display: flex; align-items: center; justify-content: center; font-family: "Roboto", sans-serif; font-weight: 700; font-size: 26px; color: var(--text-white); }
</style>
</head>
<body>
  <section class="card card--front">
    <div class="brand">
      <span class="brand__dot"></span>
      <span class="brand__name brand__name--main">Maplebrook</span>
      <span class="brand__name brand__name--sub">Pediatric Dentistry</span>
    </div>

    <div class="divider"></div>

    <div class="dentists">
      <p>Mei-Ran Tsai, <span class="credential">DMD</span></p>
      <p>Corinne Walbeck, <span class="credential">DMD</span></p>
    </div>

    <p class="address">482 Quarry Lane, Suite 517<br>Elmhaven, PA 17599</p>

    <ul class="contacts">
      <li>
        <svg viewBox="0 0 20 20" aria-hidden="true"><circle cx="10" cy="10" r="10" fill="#f0b323"/><path d="M6.5 5.2c.6-.4 1.2-.2 1.5.3l.9 1.6c.3.5.1 1-.3 1.3l-.6.4c.5 1.2 1.5 2.2 2.7 2.7l.4-.6c.3-.4.8-.6 1.3-.3l1.6.9c.5.3.7.9.3 1.5l-.6.8c-.5.6-1.3.8-2 .5-2.7-1-4.8-3.1-5.8-5.8-.3-.7-.1-1.5.5-2z" fill="#c9288c"/></svg>
        717.555.0193
      </li>
      <li>
        <svg viewBox="0 0 20 20" aria-hidden="true"><circle cx="10" cy="10" r="10" fill="#f0b323"/><rect x="5" y="6.5" width="10" height="7" rx="1" fill="#c9288c"/><path d="M5.5 7l4.5 3.5L14.5 7" stroke="#f0b323" stroke-width="1" fill="none"/></svg>
        info@maplebrookkidsdental.example
      </li>
      <li>
        <svg viewBox="0 0 20 20" aria-hidden="true"><circle cx="10" cy="10" r="10" fill="#f0b323"/><circle cx="10" cy="10" r="5" fill="none" stroke="#c9288c" stroke-width="1.3"/><path d="M5 10h10M10 5c-2 3-2 7 0 10M10 5c2 3 2 7 0 10" fill="none" stroke="#c9288c" stroke-width="1.1"/></svg>
        www.maplebrookkidsdental.example
      </li>
    </ul>

    <div class="welcome-ribbon">
      <svg viewBox="0 0 330 44" aria-hidden="true"><polygon points="0,0 330,0 314,22 330,44 0,44 16,22" fill="#f0b323"/></svg>
      <span>welcome</span>
    </div>
  </section>

  <section class="card card--back">
    <div class="brand">
      <span class="brand__dot"></span>
      <span class="brand__name brand__name--main">Maplebrook</span>
      <span class="brand__name brand__name--sub">Pediatric Dentistry</span>
    </div>
  </section>
</body>
</html>
```